Hi everyone,
Fresh Walls Co is a business that renovates older houses into modern homes. I'm looking for a design that is clean and simple. It needs to show the client that renovating is a simple process. No more than 3 colours to be used thanks.

What I need:
1. Logo
2. Business card (one side)
3. Letter head (A4)

Looking forward to the designs!

Construction

Fresh Walls Co

Sans Serif

Must have
• Trading name: Fresh Walls Co
• Contact name: Declan Ashworth
• Email: declanashworth@freshwallsco.example.com.au
• Tel: 0412 758 204
• Clean and simple
Nice to have
• If design might include a few tools. eg Hammer, paint roller etc.
Should not have
• Complicated design

```html
<!DOCTYPE html>
<html lang="en">
<head>
<meta charset="utf-8">
<title>Fresh Walls Co — Stationery</title>
<link href="https://fonts.googleapis.com/css2?family=Montserrat:wght@500;600;700&family=Roboto:wght@400;500&display=swap" rel="stylesheet">
<style>
  :root {
    --green: #8dc63f;
    --green-light: #b7d63a;
    --ink: #111111;
    --paper: #ffffff;
    --backdrop: #e4e5e7;
    --rule: #d7e6b4;
  }
  * { box-sizing: border-box; margin: 0; padding: 0; }
  html, body { width: 1200px; height: 1200px; overflow: hidden; }
  body {
    background: var(--backdrop);
    font-family: "Roboto", Arial, sans-serif;
    color: var(--ink);
    position: relative;
  }
  .brand {
    display: flex; align-items: center; gap: 10px;
    font-family: "Montserrat", Arial, sans-serif;
    font-weight: 600; color: var(--green);
    white-space: nowrap;
  }
  .brand-mark { background: var(--green); flex: none; }

  .main-logo { position: absolute; top: 110px; right: 110px; }
  .main-logo .brand { font-size: 52px; gap: 16px; }
  .main-logo .brand-mark { width: 34px; height: 34px; }

  .letterhead {
    position: absolute; left: 90px; top: 290px;
    width: 620px; height: 877px;
    background: var(--paper);
    box-shadow: 0 10px 24px rgba(0,0,0,.18);
    overflow: hidden;
  }
  .letterhead .brand { position: absolute; left: 50px; top: 80px; font-size: 26px; }
  .letterhead .brand-mark { width: 18px; height: 18px; }

  .contact-block { position: absolute; right: 50px; top: 72px; width: 220px; }
  .contact-name {
    font-family: "Montserrat", Arial, sans-serif; font-weight: 700;
    font-size: 12px; letter-spacing: .3px; margin-bottom: 10px;
  }
  .contact-line { display: flex; align-items: center; gap: 6px; font-size: 8.5px; line-height: 1.4; }
  .contact-line svg { flex: none; }

  .recipient { position: absolute; left: 60px; top: 250px; font-size: 10px; line-height: 1.35; }
  .recipient strong { font-family: "Montserrat", Arial, sans-serif; font-weight: 600; font-size: 11px; display: block; }

  .letter-body { position: absolute; left: 60px; top: 330px; width: 500px; font-size: 10.5px; line-height: 1.65; }
  .letter-body p + p { margin-top: 14px; }
  .closing { margin-top: 2px; }

  .signature {
    position: absolute; left: 60px; top: 610px;
    width: 160px; height: 44px;
    background: linear-gradient(90deg, #2a2a2a, #555);
    opacity: .85; border-radius: 3px;
  }
  .signatory { position: absolute; left: 60px; top: 668px; font-size: 11px; line-height: 1.3; font-weight: 500; }

  .band { position: absolute; left: 0; bottom: 0; display: block; }

  .business-card {
    position: absolute; left: 610px; top: 760px;
    width: 500px; height: 280px;
    background: var(--paper);
    border-radius: 14px;
    box-shadow: 0 10px 24px rgba(0,0,0,.22);
    overflow: hidden;
  }
  .business-card .brand { position: absolute; left: 30px; top: 60px; font-size: 32px; }
  .business-card .brand-mark { width: 22px; height: 22px; }
  .card-name {
    position: absolute; right: 30px; top: 142px;
    font-family: "Montserrat", Arial, sans-serif; font-weight: 700; font-size: 15px;
  }
  .card-rule { position: absolute; left: 30px; right: 30px; top: 168px; height: 1px; background: var(--rule); }
  .card-phone { position: absolute; right: 30px; top: 188px; display: flex; gap: 7px; align-items: center; font-size: 13px; }
  .card-email { position: absolute; left: 30px; top: 214px; display: flex; gap: 7px; align-items: center; font-size: 12.5px; }
</style>
</head>
<body>

<header class="main-logo">
  <div class="brand"><span class="brand-mark"></span>Fresh Walls Co</div>
</header>

<article class="letterhead">
  <div class="brand"><span class="brand-mark"></span>Fresh Walls Co</div>

  <div class="contact-block">
    <div class="contact-name">DECLAN ASHWORTH</div>
    <div class="contact-line">
      <svg width="9" height="9" viewBox="0 0 10 10"><rect width="10" height="10" rx="1.5" fill="var(--green)"/><path d="M3 2.5c0 3 1.5 4.5 4.5 5l.6-1.2-1.4-.7-.6.6c-.9-.4-1.6-1.1-2-2l.6-.6-.7-1.4z" fill="#fff"/></svg>
      0412 758 204
    </div>
    <div class="contact-line">
      <svg width="9" height="9" viewBox="0 0 10 10"><rect width="10" height="10" rx="1.5" fill="var(--green)"/><rect x="2" y="3" width="6" height="4" fill="none" stroke="#fff" stroke-width=".8"/><path d="M2 3l3 2.3L8 3" fill="none" stroke="#fff" stroke-width=".8"/></svg>
      declanashworth@freshwallsco.example.com.au
    </div>
  </div>

  <address class="recipient">
    <strong>JOHN SMITH</strong>
    Street Name, City Name.<br>Zip Code 0000
  </address>

  <div class="letter-body">
    <p>Lorem Ipsum is simply dummy text of the printing and typesetting industry. Lorem Ipsum has been the industry's standard dummy text ever since the 1500s, when an unknown printer took a galley of type and scrambled it to make a type specimen book. It has survived not only five centuries, but also the leap into electronic typesetting, remaining essentially unchanged. It was popularised in the 1960s with the release of Lettrafix sheets containing Lorem Ipsum passages, and more recently with desktop publishing software like Quill PageSetter including versions of Lorem Ipsum.</p>
    <p>It is a long established fact that a reader will be distracted by the readable content of a page when looking at its layout. The point of using Lorem Ipsum is that it has a more-or-less normal distribution of letters, as opposed to using 'Content here, content here', making it look like readable English. Many desktop publishing packages and web page editors now use Lorem Ipsum as their default model text, and a search for 'lorem ipsum' will uncover many web sites still in their infancy. Various versions have evolved over the years, sometimes by accident, sometimes on purpose (injected humour and the like).</p>
    <p class="closing">Regards,</p>
  </div>

  <div class="signature" role="img" aria-label="Handwritten signature of John Doe"></div>
  <div class="signatory">John Doe<br>General Manager</div>

  <svg class="band" width="620" height="70" viewBox="0 0 620 70" aria-hidden="true">
    <polygon points="0,40 512,40 504,70 0,70" fill="var(--ink)"/>
    <defs><linearGradient id="lhGreen" x1="0" x2="1"><stop offset="0" stop-color="var(--green)"/><stop offset="1" stop-color="var(--green-light)"/></linearGradient></defs>
    <polygon points="528,0 620,0 620,70 504,70" fill="url(#lhGreen)"/>
  </svg>
</article>

<article class="business-card">
  <div class="brand"><span class="brand-mark"></span>Fresh Walls Co</div>
  <div class="card-name">DECLAN ASHWORTH</div>
  <div class="card-rule"></div>
  <div class="card-phone">
    <svg width="16" height="16" viewBox="0 0 10 10"><rect width="10" height="10" rx="1.5" fill="var(--green)"/><path d="M3 2.5c0 3 1.5 4.5 4.5 5l.6-1.2-1.4-.7-.6.6c-.9-.4-1.6-1.1-2-2l.6-.6-.7-1.4z" fill="#fff"/></svg>
    0412 758 204
  </div>
  <div class="card-email">
    <svg width="16" height="16" viewBox="0 0 10 10"><rect width="10" height="10" rx="1.5" fill="var(--green)"/><rect x="2" y="3" width="6" height="4" fill="none" stroke="#fff" stroke-width=".8"/><path d="M2 3l3 2.3L8 3" fill="none" stroke="#fff" stroke-width=".8"/></svg>
    declanashworth@freshwallsco.example.com.au
  </div>
  <svg class="band" width="500" height="40" viewBox="0 0 500 40" aria-hidden="true">
    <defs><linearGradient id="bcGreen" x1="0" x2="1"><stop offset="0" stop-color="var(--green)"/><stop offset="1" stop-color="var(--green-light)"/></linearGradient></defs>
    <polygon points="0,28 350,28 346,40 0,40" fill="var(--ink)"/>
    <polygon points="358,0 500,0 500,40 346,40" fill="url(#bcGreen)"/>
  </svg>
</article>

</body>
</html>
```